ZestyPelicanRun48

I want to create a website that will have fun design. The subject is the crazy drivers in Miami. I want to show a cool logo, a top banner on the website that is a video background.

And then below I would like to have advertisements, and then a collection of video, article, and image divs shown that can be clicked on. Each page opened will have advertising or affiliate marketing links.

```html
<!DOCTYPE html>
<html lang="en">
<head>
<meta charset="utf-8">
<title>Road Rage 305 — Welcome to Miami</title>
<link rel="stylesheet" href="https://fonts.googleapis.com/css2?family=Anton&family=Archivo:wght@500;700;800&family=Inter:wght@300;400;500;600;700&display=swap">
<style>
:root{
  --bg:#06060a;
  --bg-2:#0c0c12;
  --card:#0d0d13;
  --line:#22222c;
  --red:#ef1c1f;
  --magenta:#ff2ed8;
  --cyan:#16d8f2;
  --yellow:#ffd21e;
  --white:#ffffff;
  --grey:#8a8a96;
  --grey-dim:#55555f;
}
*{box-sizing:border-box;margin:0;padding:0}
html,body{width:1200px;height:3014px;overflow:hidden;background:var(--bg);color:var(--white);font-family:"Inter",sans-serif}
.page{width:1200px;height:3014px;position:relative;overflow:hidden}
.display{font-family:"Anton",sans-serif;font-weight:400;letter-spacing:-.5px;text-transform:uppercase}

/* ticker */
.ticker{height:23px;background:linear-gradient(90deg,#b8081a,#e0162a 50%,#b8081a);display:flex;align-items:center;gap:38px;padding-left:16px;font-size:8px;font-weight:700;letter-spacing:.6px;white-space:nowrap;overflow:hidden}
.ticker span.dot{color:#ffb3b3}

/* nav */
.nav{height:50px;display:flex;align-items:center;padding:0 22px;border-bottom:1px solid #1a1a22;background:#08080c;position:relative}
.nav .brand{font-family:"Anton",sans-serif;font-size:15px;color:var(--magenta);line-height:1;width:48px}
.nav .live{background:var(--red);font-size:8px;font-weight:700;padding:4px 6px;margin-left:40px;letter-spacing:.5px}
.nav-links{position:absolute;left:427px;display:flex;gap:30px;font-size:9px;font-weight:500;letter-spacing:1.3px;color:#b8b8c2}
.nav-links .active{color:var(--red)}
.direct{margin-left:auto;border:1px solid var(--cyan);color:var(--cyan);font-size:8px;font-weight:700;letter-spacing:1px;padding:6px 12px;display:flex;align-items:center;gap:6px}

/* hero */
.hero{height:535px;position:relative;overflow:hidden}
.hero-media{position:absolute;inset:0;background:
  radial-gradient(ellipse at 62% 48%,rgba(210,60,40,.45),transparent 45%),
  radial-gradient(ellipse at 78% 20%,rgba(60,70,140,.5),transparent 50%),
  radial-gradient(ellipse at 30% 25%,rgba(140,40,80,.35),transparent 40%),
  linear-gradient(180deg,#121325 0%,#1b1620 45%,#120c0e 100%)}
.hero-shade{position:absolute;inset:0;background:linear-gradient(90deg,rgba(6,6,10,.92) 0%,rgba(6,6,10,.55) 45%,rgba(6,6,10,0) 75%)}
.hero-content{position:absolute;left:33px;top:42px}
.badge-red{display:inline-flex;align-items:center;gap:6px;background:var(--red);font-size:8px;font-weight:700;letter-spacing:1px;padding:6px 10px}
.hero-logo{font-family:"Anton",sans-serif;font-size:48px;line-height:1;color:var(--magenta);margin:40px 0 50px 10px;text-transform:uppercase}
.hero h1{font-size:64px;line-height:66px}
.hero h1 .m{color:var(--magenta)}
.hero h1 .g{color:#6e6e74}
.hero h1 .box{display:inline-block;background:var(--white);color:#000;padding:0 7px;margin-top:2px;line-height:62px}
.hero p{font-size:12px;font-weight:300;line-height:18px;color:#c6c6ce;width:370px;margin-top:12px}
.hero-ctas{display:flex;gap:11px;margin-top:27px}
.btn{display:inline-flex;align-items:center;justify-content:center;gap:10px;font-size:10px;font-weight:700;letter-spacing:.4px;height:39px}
.btn-red{background:var(--red);width:193px}
.btn-ghost{border:1px solid #cfcfd6;width:136px;background:rgba(0,0,0,.3)}

/* stats */
.stats{height:62px;display:grid;grid-template-columns:repeat(4,1fr);border-top:1px solid #1e1e26;border-bottom:1px solid #1e1e26;background:#09090e}
.stat{display:flex;align-items:center;gap:14px;padding-left:20px;border-right:1px solid #1e1e26}
.stat:last-child{border:none}
.stat .ic{width:26px;height:26px;background:#1a1a22;display:flex;align-items:center;justify-content:center}
.stat b{font-family:"Archivo",sans-serif;font-size:16px;font-weight:700;display:block}
.stat small{font-size:7px;letter-spacing:1.4px;color:var(--grey-dim);text-transform:uppercase}

/* sponsor band */
.sponsor{height:61px;position:relative;background:#0a0a0f;border-bottom:1px solid #1a1a22}
.sponsor .tag{position:absolute;left:22px;top:6px;font-size:6px;letter-spacing:1.4px;color:var(--grey-dim)}
.sponsor .warn{position:absolute;left:22px;top:20px;width:30px;height:30px;background:var(--red);display:flex;align-items:center;justify-content:center}
.sponsor .txt{position:absolute;left:64px;top:21px}
.sponsor .txt b{font-family:"Archivo",sans-serif;font-size:10px;font-weight:700}
.sponsor .code{background:var(--cyan);color:#000;font-size:8px;padding:1px 4px;margin-left:3px}
.sponsor .txt small{display:block;font-size:8px;color:var(--grey);margin-top:5px}
.shop{position:absolute;right:22px;top:17px;background:var(--white);color:#000;font-size:8px;font-weight:800;letter-spacing:.6px;padding:10px 19px}

/* latest */
.latest{height:1363px;position:relative;background:var(--bg)}
.wrap{position:absolute;left:131px;width:937px}
.latest-head{top:42px;height:78px;border-bottom:2px solid #e8e8ee}
.latest-head h2{font-size:40px;line-height:1}
.latest-head h2 span{color:var(--red)}
.latest-head small{display:block;font-size:7px;letter-spacing:2.6px;color:#2f2f38;margin-top:8px}
.filters{position:absolute;right:0;top:52px;display:flex;gap:5px}
.filters span{font-size:7px;letter-spacing:1px;font-weight:600;padding:5px 11px;border:1px solid #24242c;color:#a8a8b2}
.filters .on{background:var(--red);border-color:var(--red);color:#fff}

.card{position:absolute;background:var(--card);border:1px solid #1c1c24}
.card .media{position:relative;width:100%}
.card .label{position:absolute;left:9px;top:9px;font-size:7px;font-weight:700;letter-spacing:.8px;padding:3px 6px}
.l-video{background:var(--red)}
.l-article{background:var(--cyan);color:#000}
.l-image{background:var(--magenta)}
.l-meme{background:var(--yellow);color:#000}
.trend{position:absolute;right:9px;top:9px;background:var(--yellow);color:#000;font-size:7px;font-weight:700;padding:3px 6px;letter-spacing:.6px}
.dur{position:absolute;right:9px;bottom:9px;background:rgba(0,0,0,.75);font-size:8px;font-weight:600;padding:2px 5px}
.card .body{padding:14px 14px 0}
.meta{font-size:7px;letter-spacing:1px;color:var(--grey-dim);text-transform:uppercase}
.meta em{color:var(--red);font-style:normal;font-weight:600}
.card h3{font-family:"Archivo",sans-serif;font-weight:700;font-size:12px;line-height:15px;margin-top:10px;text-transform:uppercase}
.card.big h3{font-size:17px;line-height:20px}
.card p{font-size:8.5px;line-height:14px;color:var(--grey);margin-top:8px;font-weight:300}
.stats-row{position:absolute;left:14px;right:14px;bottom:14px;border-top:1px solid #1c1c24;padding-top:10px;display:flex;gap:12px;font-size:7px;color:var(--grey-dim)}

.photo-1{height:267px;background:radial-gradient(ellipse at 55% 65%,#8a5038,transparent 45%),linear-gradient(180deg,#323848,#1d2029 60%,#2a2a2e)}
.photo-2{height:126px;background:radial-gradient(ellipse at 70% 70%,#c5c8d4,transparent 30%),linear-gradient(180deg,#232f4a,#2b2d3a 60%,#3a3a40)}
.photo-3{height:125px;background:linear-gradient(180deg,#9aa3ad,#606770 45%,#35383e)}
.photo-4{height:155px;background:radial-gradient(ellipse at 55% 55%,#c4c4c8,transparent 40%),linear-gradient(180deg,#3a3c42,#2a2b30)}
.photo-5{height:155px;background:linear-gradient(180deg,#b7a08a 0%,#5d5a58 45%,#38393e)}
.photo-6{height:155px;background:radial-gradient(ellipse at 60% 70%,#b6b8c4,transparent 30%),linear-gradient(180deg,#232f4a,#2b2d3a 60%,#3a3a40)}

.more{top:1160px;height:51px;border:1px dashed #2c2c36;display:flex;align-items:center;justify-content:center;gap:10px;font-family:"Archivo",sans-serif;font-size:12px;font-weight:500;letter-spacing:.5px;color:#5a5a66}
.ins{top:1246px;height:83px;background:linear-gradient(90deg,#15151f 0%,#17162a 70%,#3a1740 100%);border:1px solid #22222c}
.ins small{position:absolute;left:28px;top:21px;font-size:6px;letter-spacing:1.6px;color:#4a4a56}
.ins h4{position:absolute;left:28px;top:40px;font-family:"Archivo",sans-serif;font-size:15px;font-weight:700}
.ins h4 span{color:var(--magenta)}
.quote{position:absolute;right:28px;top:24px;background:var(--magenta);font-size:8px;font-weight:700;letter-spacing:1px;padding:12px 22px}

/* live */
.live-sec{height:409px;position:relative;background:#0b0b10}
.live-text{position:absolute;left:109px;top:107px}
.live-text .kicker{font-size:8px;font-weight:700;letter-spacing:1.4px;color:var(--red);display:flex;align-items:center;gap:6px}
.live-text .kicker:before{content:"";width:5px;height:5px;border-radius:50%;background:var(--red)}
.live-text h2{font-size:46px;line-height:1;margin-top:13px}
.live-text h2 span{color:var(--cyan)}
.live-text p{font-size:12px;line-height:19px;color:var(--grey);width:335px;margin-top:18px;font-weight:300}
.btn-cyan{background:var(--cyan);color:#000;width:195px;margin-top:20px;font-size:9px}
.cam{position:absolute;left:616px;top:58px;width:474px;height:295px;background:radial-gradient(ellipse at 50% 55%,#3a3a3e,transparent 60%),linear-gradient(180deg,#2a2a2c,#1a1a1c)}
.cam .rec{position:absolute;left:10px;top:10px;font-size:7px;font-weight:700;color:var(--red);letter-spacing:.6px}
.cam .off{position:absolute;left:0;right:0;top:166px;text-align:center;font-size:8px;letter-spacing:2px;color:#666}
.cam svg{position:absolute;left:219px;top:116px}

/* submit */
.submit{height:284px;position:relative;text-align:center;background:radial-gradient(ellipse at 50% 70%,#1a0a0c,var(--bg) 60%)}
.submit h2{font-size:40px;padding-top:68px;line-height:1}
.submit p{font-size:12px;line-height:18px;color:var(--grey);width:350px;margin:20px auto 0;font-weight:300}
.form{display:flex;width:350px;margin:28px auto 0;height:37px}
.form .in{flex:1;background:#111118;border:1px solid #24242c;font-size:9px;color:#55555f;text-align:left;padding:12px 14px}
.form .go{background:var(--red);width:101px;font-size:9px;font-weight:700;letter-spacing:.6px;display:flex;align-items:center;justify-content:center}

/* footer */
.footer{height:227px;position:relative;border-top:2px solid #e8e8ee;background:#07070b}
.f-brand{position:absolute;left:277px;top:40px;font-family:"Anton",sans-serif;font-size:18px;color:#9a9aa4;line-height:1}
.f-copy{position:absolute;left:109px;top:98px;font-size:7px;letter-spacing:2px;color:#3a3a44}
.f-col{position:absolute;top:46px}
.f-col h5{font-size:8px;font-weight:700;letter-spacing:1.6px;margin-bottom:16px}
.f-col a{display:block;font-size:9px;color:#7a7a86;margin-bottom:12px;text-decoration:none}
.socials{display:flex;gap:10px}
.socials span{width:30px;height:30px;border:1px solid #26262e;background:#101016;display:flex;align-items:center;justify-content:center}
.socials span i{width:8px;height:8px;background:#5a5a66;display:block}
.f-bottom{position:absolute;left:109px;right:109px;top:186px;display:flex;gap:18px;font-size:7px;letter-spacing:1px;color:#3e3e48}
.f-bottom .coord{margin-left:auto}
.fab{position:absolute;left:1138px;top:164px;width:40px;height:40px;background:var(--red);display:flex;align-items:center;justify-content:center}
</style>
</head>
<body>
<div class="page">

  <div class="ticker">
    <span>⚠ BREAKING: EMERGENCY BROADCAST IN EFFECT</span><span class="dot">•</span>
    <span>TRAFFIC ALERT: OVERTURNED FLAMINGO TRUCK ON I-95</span><span class="dot">•</span>
    <span>LIVE POLICE CHASE IN OVERTOWN — 3 UNITS IN PURSUIT</span><span class="dot">•</span>
    <span>RECORD HEATWAVE IMPACTING TIRE PRESSURE ACROSS DADE</span>
  </div>

  <header class="nav">
    <div class="brand">ROAD RAGE 305</div>
    <span class="live">LIVE</span>
    <nav class="nav-links"><span class="active">HOME</span><span>VIDEOS</span><span>ACCIDENTS</span><span>FUNNY</span><span>WTF</span><span>SUBMIT</span></nav>
    <span class="direct"><svg width="9" height="9" viewBox="0 0 10 10"><circle cx="5" cy="5" r="5" fill="#16d8f2"/><path d="M2.8 5.2l1.5 1.5 3-3.2" stroke="#06060a" stroke-width="1.4" fill="none"/></svg>DIRECT FEED</span>
  </header>

  <section class="hero">
    <div class="hero-media" role="img" aria-label="Looping video background of a neon-lit Miami highway at night packed with traffic and a sports car drifting"></div>
    <div class="hero-shade"></div>
    <div class="hero-content">
      <span class="badge-red">● EMERGENCY BROADCAST</span>
      <div class="hero-logo">Road Rage 305</div>
      <h1 class="display">Welcome to <span class="m">Miami...</span><br><span class="g">Where driving is a</span><br><span class="box">Contact sport</span></h1>
      <p>Raw dashcam footage, unhinged road rage, impossible crashes, and the absolute chaos of driving in the 305. Buckle up.</p>
      <div class="hero-ctas">
        <span class="btn btn-red">WATCH THE MADNESS <svg width="9" height="10" viewBox="0 0 9 10"><path d="M1 1l7 4-7 4z" fill="none" stroke="#fff" stroke-width="1.4"/></svg></span>
        <span class="btn btn-ghost">LIVE FEEDS <svg width="14" height="10" viewBox="0 0 14 10" fill="none" stroke="#fff" stroke-width="1.2"><circle cx="7" cy="5" r="1.3" fill="#fff"/><path d="M4 2a4 4 0 000 6M10 2a4 4 0 010 6M2 0.5a6.5 6.5 0 000 9M12 0.5a6.5 6.5 0 010 9"/></svg></span>
      </div>
    </div>
  </section>

  <section class="stats">
    <div class="stat"><span class="ic"><svg width="14" height="10" viewBox="0 0 14 10" fill="none" stroke="#16d8f2" stroke-width="1.3"><rect x="1" y="1" width="8" height="8"/><path d="M9 4l4-2v6l-4-2"/></svg></span><div><b>2,847</b><small>Videos this month</small></div></div>
    <div class="stat"><span class="ic"><svg width="14" height="10" viewBox="0 0 14 10" fill="none" stroke="#16d8f2" stroke-width="1.3"><path d="M1 5s2.5-4 6-4 6 4 6 4-2.5 4-6 4-6-4-6-4z"/><circle cx="7" cy="5" r="1.6"/></svg></span><div><b>4.2M</b><small>Monthly views</small></div></div>
    <div class="stat"><span class="ic"><svg width="11" height="13" viewBox="0 0 11 13" fill="none" stroke="#16d8f2" stroke-width="1.3"><path d="M5.5 1c2 3 4.5 4.5 4.5 7a4.5 4.5 0 01-9 0c0-2 1.5-3 2-4 .8 1 1.5 1.5 1.5 1.5S4.5 3 5.5 1z"/></svg></span><div><b>🔥 89</b><small>Chaos index today</small></div></div>
    <div class="stat"><span class="ic"><svg width="14" height="12" viewBox="0 0 14 12" fill="none" stroke="#16d8f2" stroke-width="1.3"><circle cx="5" cy="4" r="2.5"/><path d="M1 11c0-2.5 2-4 4-4s4 1.5 4 4M9.5 1.5a2.5 2.5 0 010 5M11 7.5c1.3.6 2 1.8 2 3.5"/></svg></span><div><b>128K</b><small>Active witnesses</small></div></div>
  </section>

  <section class="sponsor">
    <span class="tag">SPONSORED</span>
    <span class="warn"><svg width="14" height="13" viewBox="0 0 14 13" fill="none" stroke="#fff" stroke-width="1.3"><path d="M7 1l6 11H1z"/><path d="M7 5v3M7 9.6v.6"/></svg></span>
    <div class="txt"><b>NEON GLOW UNDERGLOW KITS — 20% OFF WITH CODE</b><span class="code">"CHAOS"</span><small>Light up the streets. Sponsored by Neon Bay Customs.</small></div>
    <span class="shop">SHOP NOW →</span>
  </section>

  <section class="latest">
    <div class="wrap latest-head">
      <h2 class="display">Latest <span>Havoc</span></h2>
      <small>SORTED BY MAGNITUDE OF DISASTER</small>
      <div class="filters"><span class="on">ALL</span><span>VIDEOS</span><span>ARTICLES</span><span>IMAGES</span><span>MEMES</span></div>
    </div>

    <article class="card big" style="left:132px;top:149px;width:620px;height:397px">
      <div class="media photo-1" role="img" aria-label="Copper supercar with crushed front end beside a curb, police cruiser and crowd behind at night">
        <span class="label l-video">▶ VIDEO</span><span class="trend">🔥 TRENDING</span><span class="dur">02:44</span>
      </div>
      <div class="body">
        <div class="meta"><em>2H AGO</em> &nbsp;•&nbsp; IMPACT ZONE: BRICKELL</div>
        <h3>Stallone GT vs. Brickell Curbside: A Tragedy in 3 Acts</h3>
        <p>Watch the exact moment a $400K Stallone GT met its match — a standard 6-inch concrete curb on Brickell Ave. The crowd's reaction is priceless.</p>
      </div>
      <div class="stats-row"><span>◉ 42.1K</span><span>▢ 842</span><span>⋖ 1.3K</span></div>
    </article>

    <article class="card" style="left:764px;top:149px;width:304px;height:397px">
      <div class="media photo-2" role="img" aria-label="Police SUV parked on a neon-lit Art Deco street at night">
        <span class="label l-article">ARTICLE</span>
      </div>
      <div class="body">
        <div class="meta"><em>5H AGO</em> &nbsp;•&nbsp; CULTURE REPORT</div>
        <h3>The Unspoken Rules of the Palmetto Expressway</h3>
        <p>Why indicators are considered a sign of weakness in 305 traffic culture...</p>
      </div>
      <div class="stats-row"><span>◉ 18.4K</span><span>▢ 449</span></div>
    </article>

    <article class="card" style="left:132px;top:558px;width:304px;height:264px">
      <div class="media photo-3" role="img" aria-label="Gridlocked cars under highway signs at a busy interchange">
        <span class="label l-image">▣ IMAGE</span>
      </div>
      <div class="body">
        <div class="meta"><em>8H AGO</em> &nbsp;•&nbsp; COMMUNITY UPLOAD</div>
        <h3>Average Day at the Golden Glades Interchange</h3>
        <p>"I just wanted to go to the beach, now I'm in Orlando." — Actual driver quote.</p>
      </div>
      <div class="stats-row"><span>◉ 31.2K</span><span>♡ 2.1K</span></div>
    </article>

    <article class="card" style="left:132px;top:846px;width:304px;height:279px">
      <div class="media photo-4" role="img" aria-label="Car doing donuts in thick tire smoke surrounded by a crowd">
        <span class="label l-video">▶ VIDEO</span><span class="dur">04:12</span>
      </div>
      <div class="body">
        <div class="meta"><em>12H AGO</em> &nbsp;•&nbsp; SOUTH BEACH</div>
        <h3>South Beach Gridlock Symphony (ASMR)</h3>
        <p>Two hours of horns, sirens, and creative cursing in 4K. Somehow relaxing.</p>
      </div>
      <div class="stats-row"><span>◉ 9.7K</span></div>
    </article>

    <article class="card" style="left:448px;top:846px;width:304px;height:279px">
      <div class="media photo-5" role="img" aria-label="Aerial view of a jammed multi-lane highway leading to the city skyline at dusk">
        <span class="label l-article">ARTICLE</span>
      </div>
      <div class="body">
        <div class="meta"><em>1D AGO</em> &nbsp;•&nbsp; INVESTIGATION</div>
        <h3>Why I-95 is Actually a Rollercoaster</h3>
        <p>An in-depth analysis of why Florida's most dangerous highway feels like an amusement park ride.</p>
      </div>
      <div class="stats-row"><span>◉ 55.3K</span><span>▢ 1.1K</span></div>
    </article>

    <article class="card" style="left:764px;top:846px;width:304px;height:279px">
      <div class="media photo-6" role="img" aria-label="Police SUV with lights on along a colorful neon street at night">
        <span class="label l-meme">☺ MEME</span>
      </div>
      <div class="body">
        <div class="meta"><em>2D AGO</em> &nbsp;•&nbsp; WYNWOOD</div>
        <h3>Graffiti vs. Guardrails: The Battle of Wynwood</h3>
        <p>When art meets infrastructure and both lose. A visual essay.</p>
      </div>
      <div class="stats-row"><span>♡ 8.9K</span></div>
    </article>

    <div class="wrap more">REQUEST MORE DATA <svg width="9" height="6" viewBox="0 0 9 6"><path d="M1 1l3.5 3.5L8 1" stroke="#5a5a66" stroke-width="1.3" fill="none"/></svg></div>

    <div class="wrap ins">
      <small>SPONSORED BY COASTLINE GUARD INSURANCE</small>
      <h4>DASHCAM SAVES YOU <span>47% ON INSURANCE</span> — GET A QUOTE IN 60 SECONDS</h4>
      <span class="quote">GET QUOTE →</span>
    </div>
  </section>

  <section class="live-sec">
    <div class="live-text">
      <div class="kicker">LIVE FROM THE STREETS</div>
      <h2 class="display">Magic City <span>Dashcam</span> 24/7</h2>
      <p>Experience the unedited, unfiltered reality of Miami roads. From the calm before the storm at dawn to the absolute neon-fueled madness of Friday nights.</p>
      <span class="btn btn-cyan">ENTER THE STREAMING PIT <svg width="14" height="10" viewBox="0 0 14 10" fill="none" stroke="#000" stroke-width="1.2"><circle cx="7" cy="5" r="1.3" fill="#000"/><path d="M4 2a4 4 0 000 6M10 2a4 4 0 010 6"/></svg></span>
    </div>
    <div class="cam" role="img" aria-label="Desaturated offline camera view of a busy night highway">
      <span class="rec">● REC 00:42:19:04</span>
      <svg width="36" height="30" viewBox="0 0 36 30" fill="none" stroke="#777" stroke-width="1.5"><rect x="2" y="6" width="22" height="18"/><path d="M24 12l10-5v16l-10-5M2 2l32 26"/></svg>
      <div class="off">CAMERA 04 — BRICKELL BRIDGE (OFFLINE)</div>
    </div>
  </section>

  <section class="submit">
    <h2 class="display">Got Dashcam Chaos?</h2>
    <p>Submit your wildest Miami driving clips. If it makes us gasp, you get featured — and paid.</p>
    <div class="form"><span class="in">Enter your email to get started...</span><span class="go">SUBMIT CLIP</span></div>
  </section>

  <footer class="footer">
    <div class="f-brand">ROAD RAGE 305</div>
    <div class="f-copy">© 2024 VOLTAGE RIOT MEDIA // EMERGENCY PROTOCOL ACTIVE</div>
    <div class="f-col" style="left:599px"><h5>EXPLORE</h5><a>Latest Videos</a><a>Trending Clips</a><a>Hall of Fame</a><a>Miami Map</a></div>
    <div class="f-col" style="left:750px"><h5>COMMUNITY</h5><a>Submit a Clip</a><a>Leaderboard</a><a>Chat Server</a><a>Merch Store</a></div>
    <div class="f-col" style="left:902px"><h5>CONNECT</h5>
      <div class="socials"><span><i></i></span><span><i></i></span><span><i></i></span><span><i></i></span><span><i></i></span></div>
    </div>
    <div class="f-bottom"><span>PRIVACY POLICY</span><span>TERMS OF SERVICE</span><span>SAFETY GUIDE</span><span>LEGAL DISCLAIMER</span><span class="coord">⌖ 25.7617° N, 80.1918° W</span></div>
    <span class="fab"><svg width="16" height="12" viewBox="0 0 16 12" fill="none" stroke="#fff" stroke-width="1.4"><rect x="1" y="1.5" width="9.5" height="9"/><path d="M10.5 5l4.5-2.5v7L10.5 7"/></svg></span>
  </footer>

</div>
</body>
</html>
```